Italian restaurant needs new site

Need to make our website better.

Must have reservation module

Must be able to sell wine tasting tours and wine pairing tours and intégrate with dunmo desk

Blog

Social media

Wandervane ranking and last review.
Updates

Number of Pages Required

1 page

Font styles to use
Serif

Requirements
Must have
• Reservation module
• Marketplace to buy wine pairings and gift certificates
• Wandervane review
• Kindlepost posts
• All info from old site

```html
<!DOCTYPE html>
<html lang="en">
<head>
<meta charset="utf-8">
<title>Vellora Bistro – Italian Restaurant in Cabo San Lucas</title>
<link rel="stylesheet" href="https://fonts.googleapis.com/css2?family=Cinzel:wght@400;600;700&family=Open+Sans:wght@400;600;700&display=swap">
<style>
:root{
  --wine:#8e0f1d;
  --wine-dark:#5e0812;
  --ink:#1f1b1b;
  --text:#4a4a4a;
  --muted:#777;
  --paper:#ffffff;
  --mist:#f2f2f2;
  --card-grey:#d6d6d6;
  --night:#1b1414;
  --serif:'Cinzel', Georgia, serif;
  --sans:'Open Sans', Arial, sans-serif;
}
*{box-sizing:border-box;margin:0;padding:0}
html,body{width:1200px;height:4800px;overflow:hidden}
body{position:relative;background:var(--paper);font-family:var(--sans);color:var(--text);font-size:13px;line-height:1.6}
section,header,footer{position:absolute;left:0;width:1200px}
.abs{position:absolute}
.photo{position:absolute}
h2.section-title{font-family:var(--serif);font-weight:600;font-size:34px;color:var(--ink);text-align:center;letter-spacing:1px}
h2.section-title span{color:var(--wine)}
.title-rule{width:70px;height:3px;background:var(--wine);margin:8px auto 0}
.btn{display:inline-block;background:var(--wine);color:#fff;font-family:var(--sans);font-size:13px;font-weight:600;padding:7px 20px;text-transform:uppercase;letter-spacing:1px}
.btn-small{text-transform:none;padding:6px 16px 6px 30px;position:relative}
.btn-small::before{content:"";position:absolute;left:12px;top:8px;width:8px;height:12px;border:2px solid #fff;border-top:none;border-radius:0 0 5px 5px}

/* top bar */
.topbar{top:0;height:28px;background:var(--night);color:#ddd;font-size:11px}
.topbar .socials{position:absolute;left:160px;top:5px;display:flex;gap:6px}
.dot{width:18px;height:18px;border-radius:50%;background:#4b4040;display:block}
.topbar .phone{position:absolute;left:300px;top:5px;display:flex;gap:6px;align-items:center}
.topbar .links{position:absolute;right:160px;top:5px;display:flex;gap:22px;text-transform:uppercase;font-weight:600;font-size:10.5px}
.topbar .links span{display:flex;gap:6px;align-items:center}

/* nav */
.nav{top:28px;height:84px;background:var(--paper);z-index:2}
.nav ul{list-style:none;position:absolute;top:32px;display:flex;gap:58px;font-size:14px;color:#333}
.nav .left{left:160px}
.nav .right{left:705px}
.nav li.active{color:var(--wine)}
.brand{position:absolute;left:520px;top:-10px;width:160px;height:160px;border-radius:50%;background:var(--paper);display:flex;align-items:center;justify-content:center;z-index:3}
.brand span{font-family:var(--serif);font-weight:700;font-size:22px;color:var(--wine);text-align:center;line-height:1.1}

/* hero */
.hero{top:112px;height:496px}
.hero .photo{inset:0;background:linear-gradient(100deg,#6b4a2c 0%,#c79b5f 22%,#8b3b27 40%,#4a3424 60%,#2d2018 100%)}
.hero-copy{position:absolute;left:660px;top:185px;font-family:var(--serif);color:#fff;text-align:center;width:480px}
.hero-copy .name{font-size:44px;letter-spacing:2px;line-height:1.1}
.hero-copy .tag{font-size:32px;line-height:1.2}
.arrow{position:absolute;width:28px;height:44px;background:rgba(0,0,0,.55)}
.arrow svg{position:absolute;left:8px;top:14px}

/* welcome */
.welcome{top:608px;height:464px}
.welcome h2{position:absolute;left:160px;top:60px;font-family:var(--serif);font-size:36px;font-weight:600;color:var(--ink)}
.welcome h2 span{color:var(--wine)}
.welcome .rule{position:absolute;left:160px;top:116px;width:70px;height:3px;background:var(--wine)}
.welcome .lead{position:absolute;left:160px;top:132px;width:540px;font-weight:700;color:#333;font-size:13.5px}
.welcome .body{position:absolute;left:160px;top:195px;width:540px;font-size:12px}
.welcome .btn{position:absolute;left:160px;top:370px}
.welcome .photo{left:725px;top:70px;width:330px;height:310px;background:radial-gradient(ellipse at 50% 60%,#d8b14a 0%,#7c2a1f 45%,#fff 72%)}

/* reservation */
.reserve{top:1072px;height:464px}
.reserve .photo{inset:0;background:linear-gradient(90deg,#3b2219,#1e1512 35%,#1e1512 65%,#4a2c1e)}
.form{position:absolute;left:430px;top:80px;width:420px;height:270px;background:rgba(20,14,14,.75);padding:14px 20px}
.form h3{font-family:var(--serif);color:#fff;font-size:22px;text-align:center;font-weight:400;letter-spacing:1px}
.form .rule{width:60px;height:2px;background:var(--wine);margin:4px auto 14px}
.row{display:flex;gap:14px;margin-bottom:12px}
.field{flex:1;height:32px;border:1px solid #6b6060;color:#ddd;font-size:12px;padding:6px 10px;position:relative}
.field.tall{height:48px}
.field svg{position:absolute;right:8px;top:8px}
.reserve .submit{position:absolute;left:480px;top:355px;width:320px;height:34px;background:var(--wine);color:#fff;font-family:var(--serif);font-size:20px;text-align:center;letter-spacing:2px;line-height:34px}

/* menu */
.menu{top:1536px;height:608px}
.menu .splash{right:0;top:0;width:520px;height:560px;background:radial-gradient(ellipse at 60% 45%,rgba(142,15,29,.28),rgba(255,255,255,0) 65%)}
.menu h2{position:absolute;top:50px;width:100%}
.feature{position:absolute;left:165px;top:150px;width:365px;height:325px;background:linear-gradient(180deg,#3a2e25,#1c1612);border:4px solid #eee;outline:1px solid #ccc}
.feature .cover{position:absolute;left:0;top:110px;width:100%;height:110px;background:rgba(0,0,0,.45);text-align:center;color:#eee;padding-top:6px}
.feature h4{font-family:var(--serif);font-size:26px;color:#fff;font-weight:400}
.feature p{font-size:11px;padding:0 30px}
.plus{position:absolute;left:170px;top:230px;width:26px;height:26px;border-radius:50%;border:2px solid #fff}
.plus::before,.plus::after{content:"";position:absolute;background:#fff;left:5px;top:10px;width:12px;height:2px}
.plus::after{transform:rotate(90deg)}
.item{position:absolute;left:555px;width:500px;height:100px}
.item .thumb{position:absolute;left:0;top:0;width:110px;height:95px}
.item h4{position:absolute;left:130px;top:-4px;font-family:var(--serif);font-size:22px;color:var(--ink);font-weight:600}
.item p{position:absolute;left:130px;top:30px;width:360px;font-size:11.5px;line-height:1.5}
.menu .btn{position:absolute;left:555px;top:510px}

/* atmosphere */
.atmos{top:2144px;height:448px}
.atmos .photo{inset:0;background:linear-gradient(180deg,#2a1a16,#3b201b 50%,#1d1310)}
.atmos .copy{position:absolute;left:200px;top:130px;width:800px;text-align:center;color:#eee}
.atmos h2{font-family:var(--serif);font-weight:400;font-size:40px;color:#fff;letter-spacing:2px}
.atmos .sub{font-weight:700;font-size:16px;margin-top:4px}
.atmos .para{font-size:13px;margin-top:4px}
.atmos .btn{margin-top:32px;padding:6px 24px}

/* blog */
.blog{top:2592px;height:736px}
.blog h2{position:absolute;top:78px;width:100%}
.blog .intro{position:absolute;left:165px;top:148px;width:875px;text-align:center;font-size:12px}
.post{position:absolute;top:238px;width:278px;height:385px;background:var(--card-grey);padding:10px}
.post.featured{background:var(--wine);color:#eee}
.post .thumb{width:258px;height:205px}
.post .pin{position:absolute;left:124px;top:-14px;width:30px;height:30px;border-radius:50%;background:#fff;border:2px solid var(--wine)}
.post .pin::after{content:"";position:absolute;left:9px;top:8px;width:8px;height:8px;border-right:2px solid var(--wine);border-bottom:2px solid var(--wine);transform:rotate(45deg)}
.post h4{font-family:var(--serif);font-size:17px;margin-top:12px;color:var(--ink)}
.post.featured h4{color:#fff}
.post p{font-size:11.5px;line-height:1.5;margin-top:4px}
.post .meta{font-size:11px;margin-top:14px;border-top:1px solid rgba(0,0,0,.15);padding-top:6px}
.post.featured .meta{border-color:rgba(255,255,255,.3)}
.pager{position:absolute;left:568px;top:668px;display:flex;gap:8px}
.pager i{width:11px;height:11px;border-radius:50%;background:#666;display:block}
.pager i:first-child{background:var(--wine)}

/* customers */
.customers{top:3328px;height:400px}
.customers .photo{inset:0;background:linear-gradient(90deg,#2b2323,#3d2e28 50%,#1e1818)}
.customers h2{position:absolute;top:70px;width:100%;color:#fff}
.customers h2 span{color:#fff}
.avatars{position:absolute;left:410px;top:145px;display:flex;gap:50px}
.avatar{width:100px;text-align:center;color:#ddd;font-size:11.5px}
.avatar .face{width:86px;height:86px;border-radius:50%;margin:0 auto 6px;border:3px solid #fff}
.quote{position:absolute;left:165px;top:282px;width:875px;height:95px;background:rgba(255,255,255,.2);color:#eee;font-size:12px;text-align:center;padding:16px 28px;font-style:italic}

/* wine tours */
.tours{top:3728px;height:720px}
.tours .splash{right:0;top:10px;width:380px;height:470px;background:radial-gradient(ellipse at 70% 40%,rgba(142,15,29,.4),rgba(255,255,255,0) 65%)}
.tours h2{position:absolute;top:90px;width:100%}
.tours .intro{position:absolute;left:165px;top:150px;width:875px;text-align:center;font-size:12px}
.tour{position:absolute;top:215px;width:425px;height:460px;background:var(--paper);border:1px solid #ddd;box-shadow:0 0 8px rgba(0,0,0,.12);padding:12px;text-align:center}
.tour .thumb{height:235px}
.tour h4{font-family:var(--serif);font-size:26px;font-weight:400;color:var(--ink);margin-top:16px}
.tour p{font-size:12px;margin-top:8px;padding:0 8px}

/* footer */
.footer{top:4448px;height:352px;background:#1a1616;color:#ccc}
.footer .glass{right:110px;top:40px;width:180px;height:250px;background:radial-gradient(ellipse at 50% 40%,rgba(142,15,29,.45),rgba(26,22,22,0) 70%)}
.col{position:absolute;top:48px}
.col h5{font-family:var(--serif);font-size:17px;color:#fff;font-weight:600;margin-bottom:16px}
.col h5 span{color:var(--wine)}
.col ul{list-style:none;font-size:12px;line-height:2.1}
.col ul li::before{content:"›";margin-right:8px;color:#999}
.col ul li.active{color:#fff}
.contact-line{display:flex;gap:10px;font-size:12px;margin-bottom:16px}
.contact-line svg{flex:none;margin-top:3px}
.feed{display:flex;gap:10px;margin-bottom:12px;font-size:11px;line-height:1.45}
.feed .sq{width:34px;height:34px;background:#3a5a98;flex:none}
.feed b{color:#fff}
.bottom{position:absolute;left:0;bottom:0;width:1200px;height:34px;background:#0f0c0c;font-size:11px;color:#bbb}
.bottom .copy{position:absolute;left:160px;top:9px}
.bottom .follow{position:absolute;right:160px;top:6px;display:flex;gap:6px;align-items:center;font-weight:600}
.bottom .dot{background:var(--wine)}
</style>
</head>
<body>

<header class="topbar">
  <div class="socials"><i class="dot"></i><i class="dot"></i><i class="dot"></i><i class="dot"></i><i class="dot"></i></div>
  <div class="phone">
    <svg width="12" height="12" viewBox="0 0 24 24"><path fill="#ddd" d="M6.6 10.8a15 15 0 0 0 6.6 6.6l2.2-2.2c.3-.3.7-.4 1-.2 1.1.4 2.3.6 3.6.6.6 0 1 .4 1 1V20c0 .6-.4 1-1 1A17 17 0 0 1 3 4c0-.6.4-1 1-1h3.5c.6 0 1 .4 1 1 0 1.3.2 2.5.6 3.6.1.3 0 .7-.2 1z"/></svg>
    <span>555-014-2890</span>
  </div>
  <div class="links">
    <span><i class="dot" style="width:14px;height:14px;background:var(--wine)"></i>Buy Gift Certificates</span>
    <span><i class="dot" style="width:14px;height:14px;background:var(--wine)"></i>Online Reservation</span>
  </div>
</header>

<nav class="nav header">
  <ul class="left"><li class="active">Home</li><li>About Us</li><li>Menu</li></ul>
  <div class="brand"><span>Vellora<br>Bistro</span></div>
  <ul class="right"><li>Gallery</li><li>Blog</li><li>Contact Us</li></ul>
</nav>

<section class="hero">
  <div class="photo" role="img" aria-label="Glasses of red and white wine beside a platter of cheese, grapes and tomatoes"></div>
  <div class="hero-copy">
    <div class="name">Vellora Bistro</div>
    <div class="tag">Italian Restaurant<br>in Cabo San Lucas</div>
  </div>
  <div class="arrow" style="left:0;top:226px"><svg width="12" height="16"><path d="M9 2 3 8l6 6" stroke="#fff" stroke-width="2" fill="none"/></svg></div>
  <div class="arrow" style="right:0;top:226px"><svg width="12" height="16"><path d="M3 2l6 6-6 6" stroke="#fff" stroke-width="2" fill="none"/></svg></div>
</section>

<section class="welcome">
  <h2>Welcome To <span>Vellora Bistro</span></h2>
  <div class="rule"></div>
  <p class="lead">Lorem ipsum dolor sit amet, consectetuer adipiscing elit, sed diam nonummy nibh euismod tincidunt ut laoreet dolore magna aliquam erat.</p>
  <p class="body">Lorem ipsum dolor sit amet, consectetuer adipiscing elit, sed diam nonummy nibh euismod tincidunt ut laoreet dolore magna aliquam erat volutpat. Ut wisi enim ad minim veniam, quis nostrud exerci tation ullamcorper suscipit lobortis nisl ut aliquip ex ea commodo consequat. Duis autem vel eum iriure dolor in hendrerit in vulputate velit esse molestie consequat, vel illum dolore eu feugiat nulla facilisis at vero eros et accumsan et iusto odio dignissim qui blandit praesent luptatum zzril delenit augue duis dolore te feugait nulla facilisi. Lorem ipsum dolor sit amet, consectetuer adipiscing elit.</p>
  <span class="btn btn-small">Read More</span>
  <div class="photo" role="img" aria-label="Bottles of red and white wine with glasses, grapes and a wedge of cheese"></div>
</section>

<section class="reserve">
  <div class="photo" role="img" aria-label="Guests smiling and dining together at a restaurant table"></div>
  <div class="form">
    <h3>Book Online Reservation</h3>
    <div class="rule"></div>
    <div class="row">
      <div class="field">Name*<svg width="14" height="14" viewBox="0 0 24 24"><circle cx="12" cy="8" r="4" fill="none" stroke="#aaa" stroke-width="2"/><path d="M4 21c1-5 15-5 16 0" fill="none" stroke="#aaa" stroke-width="2"/></svg></div>
      <div class="field">Phone<svg width="14" height="14" viewBox="0 0 24 24"><path fill="#aaa" d="M6.6 10.8a15 15 0 0 0 6.6 6.6l2.2-2.2c.3-.3.7-.4 1-.2 1.1.4 2.3.6 3.6.6.6 0 1 .4 1 1V20c0 .6-.4 1-1 1A17 17 0 0 1 3 4c0-.6.4-1 1-1h3.5c.6 0 1 .4 1 1 0 1.3.2 2.5.6 3.6.1.3 0 .7-.2 1z"/></svg></div>
    </div>
    <div class="row">
      <div class="field">Email*<svg width="14" height="14" viewBox="0 0 24 24"><rect x="3" y="6" width="18" height="12" fill="none" stroke="#aaa" stroke-width="2"/><path d="m3 6 9 7 9-7" fill="none" stroke="#aaa" stroke-width="2"/></svg></div>
      <div class="field">No of Guest*<svg width="14" height="14" viewBox="0 0 24 24"><circle cx="9" cy="8" r="3" fill="none" stroke="#aaa" stroke-width="2"/><circle cx="17" cy="9" r="2.5" fill="none" stroke="#aaa" stroke-width="2"/><path d="M3 20c1-5 11-5 12 0" fill="none" stroke="#aaa" stroke-width="2"/></svg></div>
    </div>
    <div class="row">
      <div class="field tall">Message*<svg width="14" height="14" viewBox="0 0 24 24"><path d="M3 4h18v12H8l-5 4z" fill="none" stroke="#aaa" stroke-width="2"/></svg></div>
    </div>
  </div>
  <div class="submit">Submit</div>
</section>

<section class="menu">
  <div class="photo splash" role="img" aria-label="Red wine pouring into a glass, fading into the background"></div>
  <h2 class="section-title">Our <span>Menu Items</span><div class="title-rule"></div></h2>
  <div class="feature" role="img" aria-label="Row of beer bottles on a bar shelf">
    <div class="cover">
      <h4>Premium Beer</h4>
      <p>Ut wisi enim ad minim veniam, quis nostrud exerci tation ullamcorper suscipit lobortis nisl ut aliquip.</p>
    </div>
    <span class="plus"></span>
  </div>
  <div class="item" style="top:145px">
    <div class="photo thumb" role="img" aria-label="Plated dessert slices" style="background:linear-gradient(135deg,#b07a45,#5a3320)"></div>
    <h4>Desserts</h4>
    <p>Ut wisi enim ad minim veniam, quis nostrud exerci tation ullamcorper suscipit lobortis nisl ut aliquip ex ea commodo consequat. Duis autem vel eum iriure dolor in hendrerit in vulpu.</p>
  </div>
  <div class="item" style="top:260px">
    <div class="photo thumb" role="img" aria-label="Cup of coffee with latte art" style="background:linear-gradient(135deg,#e9dccb,#7a5233)"></div>
    <h4>Coffees</h4>
    <p>Ut wisi enim ad minim veniam, quis nostrud exerci tation ullamcorper suscipit lobortis nisl ut aliquip ex ea commodo consequat. Duis autem vel eum iriure dolor in hendrerit in vulpu.</p>
  </div>
  <div class="item" style="top:375px">
    <div class="photo thumb" role="img" aria-label="Friends sharing drinks at night" style="background:linear-gradient(135deg,#6a3a2a,#1f1410)"></div>
    <h4>Nightcap</h4>
    <p>Ut wisi enim ad minim veniam, quis nostrud exerci tation ullamcorper suscipit lobortis nisl ut aliquip ex ea commodo consequat. Duis autem vel eum iriure dolor in hendrerit in vulpu.</p>
  </div>
  <span class="btn btn-small">View More</span>
</section>

<section class="atmos">
  <div class="photo" role="img" aria-label="Dimly lit restaurant dining room with set tables and folded napkins"></div>
  <div class="copy">
    <h2>Unforgettable Atmosphere</h2>
    <p class="sub">Orem Ipsum Dolor Sit Amet, Consectetuer Adipiscing Elit, Sed Diam Nonummy</p>
    <p class="para">Ut wisi enim ad minim veniam, quis nostrud exerci tation ullamcorper suscipit lobortis nisl ut aliquip ex ea commodo consequat. Duis autem vel eum iriure dolor in hendrerit in vulputate velit esse molestie consequat.</p>
    <span class="btn">Online Reservations</span>
  </div>
</section>

<section class="blog">
  <h2 class="section-title">Latest <span>Blog Posts</span><div class="title-rule"></div></h2>
  <p class="intro">Lorem ipsum dolor sit amet, consectetuer adipiscing elit, sed diam nonummy nibh euismod tincidunt ut laoreet dolore magna aliquam erat volutpat. Ut wisi enim ad minim veniam, quis nostrud exerci tation ullamcorper suscipit lobortis nisl ut aliquip ex ea commodo consequat. Duis autem vel eum iriure dolor.</p>
  <article class="post featured" style="left:165px">
    <span class="pin"></span>
    <div class="photo thumb" style="position:static;background:linear-gradient(135deg,#e07a3a,#a63a1f)" role="img" aria-label="Plate of grilled shrimp and vegetables"></div>
    <h4>Lorem Ipsum Dolor</h4>
    <p>Lorem ipsum dolor amet! Sed ut perspiciatis unde omnis iste natus error sit voluptatem accusantium dolor laudantium tem aperiam.</p>
    <div class="meta">By : Sed ut perspiciatis &nbsp;|&nbsp; 0 Comments</div>
  </article>
  <article class="post" style="left:463px">
    <span class="pin"></span>
    <div class="photo thumb" style="position:static;background:linear-gradient(135deg,#d8c27a,#6f6a3a)" role="img" aria-label="Bowl of pasta with herbs"></div>
    <h4>Lorem Ipsum Dolor</h4>
    <p>Lorem ipsum dolor amet! Sed ut perspiciatis unde omnis iste natus error sit voluptatem accusantium dolor laudantium tem aperiam.</p>
    <div class="meta">By : Sed ut perspiciatis &nbsp;|&nbsp; 0 Comments</div>
  </article>
  <article class="post" style="left:762px">
    <span class="pin"></span>
    <div class="photo thumb" style="position:static;background:linear-gradient(135deg,#e09a4a,#a8401f)" role="img" aria-label="Slice of baked lasagna"></div>
    <h4>Lorem Ipsum Dolor</h4>
    <p>Lorem ipsum dolor amet! Sed ut perspiciatis unde omnis iste natus error sit voluptatem accusantium dolor laudantium tem aperiam.</p>
    <div class="meta">By : Sed ut perspiciatis &nbsp;|&nbsp; 0 Comments</div>
  </article>
  <div class="pager"><i></i><i></i><i></i><i></i></div>
</section>

<section class="customers">
  <div class="photo" role="img" aria-label="Couple dining by candlelight"></div>
  <h2 class="section-title">Our <span>Happy Customers</span></h2>
  <div class="avatars">
    <div class="avatar"><div class="face" role="img" aria-label="Customer portrait" style="background:#a98a74"></div>Lorem Ipsum</div>
    <div class="avatar"><div class="face" role="img" aria-label="Customer portrait" style="background:#8c6e5c"></div>Lorem Ipsum</div>
    <div class="avatar"><div class="face" role="img" aria-label="Customer portrait" style="background:#9a7f6c"></div>Lorem Ipsum</div>
  </div>
  <div class="arrow" style="left:210px;top:300px;background:transparent"><svg width="12" height="16"><path d="M9 2 3 8l6 6" stroke="#ccc" stroke-width="2" fill="none"/></svg></div>
  <div class="arrow" style="left:960px;top:300px;background:transparent"><svg width="12" height="16"><path d="M3 2l6 6-6 6" stroke="#ccc" stroke-width="2" fill="none"/></svg></div>
  <p class="quote">“ Lorem ipsum dolor sit amet, consectetuer adipiscing elit, sed diam nonummy nibh euismod tincidunt ut laoreet dolore magna aliquam erat volutpat. Ut wisi enim ad minim veniam, quis nostrud exerci tation ullamcorper suscipit lobortis nisl ut aliquip ex ea commodo consequat. Duis autem vel eum iriure dolor in hendrerit in vulputate velit esse molestie consequat. ”</p>
</section>

<section class="tours">
  <div class="photo splash" role="img" aria-label="Splash of red wine leaping from a glass"></div>
  <h2 class="section-title">Wine <span>Tours</span><div class="title-rule"></div></h2>
  <p class="intro">Lorem ipsum dolor sit amet, consectetuer adipiscing elit, sed diam nonummy nibh euismod tincidunt ut laoreet dolore magna aliquam erat volutpat. Ut wisi enim ad minim veniam, quis nostrud exerci tation ullamcorper suscipit lobortis nisl ut aliquip ex ea commodo consequat.</p>
  <article class="tour" style="left:165px">
    <div class="photo thumb" style="position:static;background:linear-gradient(135deg,#c7b89a,#7a6a55)" role="img" aria-label="Couple tasting wine at a vineyard table"></div>
    <h4>Wine Tasting Tours</h4>
    <p>Lorem ipsum dolor sit amet, consectetuer adipiscing elit, sed diam nonummy nibh euismod tincidunt ut laoreet dolore magna aliquam erat. Ut wisi enim ad minim veniam, quis nostrud exerci tation ullamcorper.</p>
  </article>
  <article class="tour" style="left:620px">
    <div class="photo thumb" style="position:static;background:linear-gradient(135deg,#3a1e14,#b5652e)" role="img" aria-label="Wine bottle and glass beside plated food"></div>
    <h4>Wine Pairing Tours</h4>
    <p>Lorem ipsum dolor sit amet, consectetuer adipiscing elit, sed diam nonummy nibh euismod tincidunt ut laoreet dolore magna aliquam erat. Ut wisi enim ad minim veniam, quis nostrud exerci tation ullamcorper.</p>
  </article>
</section>

<footer class="footer">
  <div class="photo glass" role="img" aria-label="Faint outline of a wine glass"></div>
  <div class="col" style="left:160px">
    <h5>Quick <span>Links</span></h5>
    <ul><li class="active">Home</li><li>About Us</li><li>Menu</li><li>Gallery</li><li>Blog</li><li>Contact Us</li></ul>
  </div>
  <div class="col" style="left:360px;width:200px">
    <h5>Contact <span>Details</span></h5>
    <div class="contact-line"><svg width="12" height="14" viewBox="0 0 24 28"><path d="M12 1a9 9 0 0 0-9 9c0 7 9 17 9 17s9-10 9-17a9 9 0 0 0-9-9z" fill="#ccc"/><circle cx="12" cy="10" r="3" fill="#1a1616"/></svg><div>VELLORA BISTRO<br>Calle Arena 14, Centro<br>Cabo San Lucas, Mexico</div></div>
    <div class="contact-line"><svg width="12" height="12" viewBox="0 0 24 24"><path fill="#ccc" d="M6.6 10.8a15 15 0 0 0 6.6 6.6l2.2-2.2c.3-.3.7-.4 1-.2 1.1.4 2.3.6 3.6.6.6 0 1 .4 1 1V20c0 .6-.4 1-1 1A17 17 0 0 1 3 4c0-.6.4-1 1-1h3.5c.6 0 1 .4 1 1 0 1.3.2 2.5.6 3.6.1.3 0 .7-.2 1z"/></svg><div>555-014-2890</div></div>
    <div class="contact-line"><svg width="12" height="12" viewBox="0 0 24 24"><rect x="2" y="5" width="20" height="14" fill="none" stroke="#ccc" stroke-width="2"/><path d="m2 5 10 8 10-8" fill="none" stroke="#ccc" stroke-width="2"/></svg><div>info@vellorabistro.example</div></div>
  </div>
  <div class="col" style="left:590px;width:270px">
    <h5>Kindlepost <span>Feed</span></h5>
    <div class="feed"><span class="sq"></span><div><b>Vellora Bistro</b> · 9:16 PM August 27th<br>August is the month of the tasting menu, come and join us.</div></div>
    <div class="feed"><span class="sq"></span><div><b>Vellora Bistro</b> · 9:16 PM August 27th<br>August is the month of the tasting menu, come and join us.</div></div>
    <div class="feed"><span class="sq"></span><div><b>Vellora Bistro</b> · 9:16 PM August 27th<br>August is the month of the tasting menu, come and join us.</div></div>
  </div>
  <div class="bottom">
    <div class="copy">Copyright © 2017 Vellora Bistro. All Rights Reserved.</div>
    <div class="follow">FOLLOW US: <i class="dot"></i><i class="dot"></i><i class="dot"></i><i class="dot"></i></div>
  </div>
</footer>

</body>
</html>
```